Brightwave Reach - Business Card

We need a business card for a Social Media Marketing company that specializes in online marketing for small businesses in Canada using common Social Media platforms such as Pixlora, Chatterly, Blinkpost & Quibber.

I have uploaded a copy of our logo which I would like utilized in the business card. We would like the business card to be modern yet classy design.

Our website is www.brightwavereach.ca

Industry/Entity Type

Marketing

Contact Information for Business Card

Email: info@brightwavereach.ca
Website: www.brightwavereach.ca
Telephone: 604-555-0193

Colors

Designer to choose colors to be used in the design.

Requirements
Must have
• Social Media icons on reverse
• Please add some designs with color.

```html
<!DOCTYPE html>
<html lang="en">
<head>
<meta charset="utf-8">
<title>Brightwave Reach – Business Card</title>
<link rel="stylesheet" href="https://fonts.googleapis.com/css2?family=Roboto:wght@400;500&family=Roboto+Condensed:wght@500;700&display=swap">
<style>
  :root {
    --backdrop: #222324;
    --slate: #3d4245;
    --paper: #f1f1f1;
    --ink: #3a3d40;
    --muted: #a9abad;
    --frame: #4a4d50;
  }
  html, body {
    margin: 0;
    padding: 0;
    width: 1200px;
    height: 960px;
    overflow: hidden;
    background: var(--backdrop);
  }
  .canvas {
    position: relative;
    width: 1200px;
    height: 960px;
  }
  .card {
    position: absolute;
    width: 600px;
    height: 342px;
    box-shadow: 0 3px 10px rgba(0,0,0,.45);
  }
  .card--front {
    left: 314px;
    top: 113px;
    background: var(--slate);
  }
  .card--back {
    left: 311px;
    top: 472px;
    height: 343px;
    background: var(--paper);
  }
  .brand-name {
    position: absolute;
    margin: 0;
    font-family: "Roboto Condensed", sans-serif;
    font-weight: 700;
    text-transform: uppercase;
    text-align: center;
    line-height: 1;
    letter-spacing: 0.5px;
  }
  .card--front .brand-name {
    left: 40px;
    top: 132px;
    width: 212px;
    font-size: 31px;
    color: #ffffff;
  }
  .card--back .brand-name {
    left: 180px;
    top: 127px;
    width: 240px;
    font-size: 34px;
    color: var(--ink);
  }
  .contact-panel {
    position: absolute;
    left: 293px;
    top: 15px;
    width: 291px;
    height: 314px;
    background: var(--paper);
    border-radius: 10px;
  }
  .contact-panel__frame {
    position: absolute;
    left: 8px;
    top: 8px;
    right: 8px;
    bottom: 8px;
    border: 3px solid var(--frame);
    border-radius: 2px;
  }
  .contact-panel__frame::after {
    content: "";
    position: absolute;
    left: 3px;
    top: 3px;
    right: 3px;
    bottom: 3px;
    border: 1.5px solid var(--frame);
  }
  .person {
    position: absolute;
    left: 57px;
    top: 94px;
  }
  .person__name {
    margin: 0;
    font-family: "Roboto Condensed", sans-serif;
    font-weight: 500;
    font-size: 21px;
    color: var(--ink);
    line-height: 24px;
  }
  .person__title {
    margin: 0;
    font-family: "Roboto Condensed", sans-serif;
    font-weight: 500;
    font-size: 14px;
    color: var(--muted);
    line-height: 18px;
  }
  .contact-list {
    position: absolute;
    left: 57px;
    top: 160px;
    margin: 0;
    padding: 0;
    list-style: none;
    font-family: "Roboto", sans-serif;
    font-size: 14px;
    color: var(--ink);
  }
  .contact-list li {
    display: flex;
    align-items: center;
    height: 19.5px;
  }
  .contact-list svg {
    width: 12px;
    height: 12px;
    margin-right: 9px;
    fill: var(--ink);
  }
  .social-row {
    position: absolute;
    left: 0;
    right: 0;
    top: 285px;
    display: flex;
    justify-content: center;
    gap: 18px;
    font-family: "Roboto", sans-serif;
    font-size: 13px;
    color: var(--ink);
  }
  .social-row span {
    display: flex;
    align-items: center;
  }
  .social-row span::before {
    content: "";
    width: 8px;
    height: 8px;
    border: 1.5px solid var(--ink);
    border-radius: 50%;
    margin-right: 6px;
  }
</style>
</head>
<body>
<main class="canvas">
  <section class="card card--front">
    <h1 class="brand-name">Brightwave<br>Reach</h1>
    <div class="contact-panel">
      <div class="contact-panel__frame"></div>
      <div class="person">
        <p class="person__name">DANIEL HART</p>
        <p class="person__title">CEO/FOUNDER</p>
      </div>
      <ul class="contact-list">
        <li>
          <svg viewBox="0 0 24 24"><path d="M6.6 10.8a15.1 15.1 0 0 0 6.6 6.6l2.2-2.2a1 1 0 0 1 1-.25 11.4 11.4 0 0 0 3.6.57 1 1 0 0 1 1 1V20a1 1 0 0 1-1 1A17 17 0 0 1 3 4a1 1 0 0 1 1-1h3.5a1 1 0 0 1 1 1c0 1.25.2 2.45.57 3.57a1 1 0 0 1-.25 1z"/></svg>
          604-555-0193
        </li>
        <li>
          <svg viewBox="0 0 24 24"><path d="M2 5h20v14H2z M3.5 6.5 12 12.5l8.5-6" fill="none" stroke="#3a3d40" stroke-width="2"/><path d="M2 5h20L12 12z"/></svg>
          info@brightwavereach.ca
        </li>
        <li>
          <svg viewBox="0 0 24 24"><circle cx="12" cy="12" r="10"/><path d="M2 12h20M12 2c3 3 3 17 0 20M12 2c-3 3-3 17 0 20" fill="none" stroke="#f1f1f1" stroke-width="1.6"/></svg>
          www.brightwavereach.ca
        </li>
      </ul>
    </div>
  </section>

  <section class="card card--back">
    <h2 class="brand-name">Brightwave<br>Reach</h2>
    <div class="social-row">
      <span>Chatterly</span>
      <span>Pixlora</span>
      <span>Quibber</span>
    </div>
  </section>
</main>
</body>
</html>
```